Wordpress - For IT, Cloud/Hosting, Residential/Commercial Construction Services

We are a holding company for service companies. We want the current Wordpress site modified or a new wordpress site completed. We want this site to be the parent website, that then has pull down menus linking to our other website (currently http://brightwallfix.com, http://q7v.host and would like it to be easy and fluid as we acquire more companies as we have with TKLS, Inc., B&J Construction, Brightwall Fix etc. Model after sites like Pemrose.com, Tallowbine.com, QDV.com,.vanterelm.com

------

The parent is the main site q7v Corp. Below that are sub corps and DBAs. q7v Corp stands for Quick 7 Venture Corp. q7v Offers IT manages services, 24x7 support, Monitoring NOC, Remote Hands, Onsite support services. We have acquired TKLS, Inc, B & J Construction, BrightwallFix.com. We plan to acquire/spin up many companies that offer service, support and installation offerings and will all be known as an q7v Corp Company for branding purposes. We recently had our logo done, but then ran it through 3d glass as we like the look better than the original works. We have original files in vector, but not the 3D galss door render.

Target Market(s)

IT Server and Desktop Support. Construction. Mold Remediation. Mergers and Acquisitions.

Industry/Entity Type

It Company

Coding

Coded - Design and coding required

Font styles to use
Sans Serif

Colors
0792cd

Requirements
Must have
• Clean interface. Modern design. Mobile device and multi browser support. Must be for Wordpress. Job posting with resume submission module.Hook to our Web hosting portal (Tormund) API into VexaLine Reseller portal, customer portal to allow payments to their account etc.. Easy to edit. Easy to add to, Press Release Section, Investor Relations etc.
Should not have
• Slow loading. Played out design. Over use of stock images. Copied from a competitor or something point to such.

```html
<!DOCTYPE html>
<html lang="en">
<head>
<meta charset="utf-8">
<title>Q7V Corp</title>
<link href="https://fonts.googleapis.com/css2?family=Roboto+Slab:wght@300;400;700&family=Roboto:wght@400;500&display=swap" rel="stylesheet">
<style>
:root{
  --blue:#0d7bcb;
  --blue-band:#0f7bc9;
  --ink:#1b1b1b;
  --text:#333;
  --muted:#8a8a8a;
  --grey-btn:#6b6b6b;
  --line:#dcdcdc;
  --white:#fff;
  --dark:#1a2230;
}
*{margin:0;padding:0;box-sizing:border-box}
html,body{width:1200px;height:2835px;overflow:hidden;background:var(--white)}
body{position:relative;font-family:"Roboto Slab",serif;color:var(--text)}
.abs{position:absolute}

/* header */
.site-header{position:absolute;left:0;top:0;width:1200px;height:78px;border-bottom:3px solid var(--blue);background:var(--white)}
.brand{position:absolute;left:172px;top:14px;color:var(--blue);font-weight:700;line-height:1}
.brand .mark{font-size:30px;letter-spacing:1px;display:block}
.brand .sub{font-size:11px;letter-spacing:9px;display:block;margin-top:2px}
.main-nav{position:absolute;top:32px;left:0;font-family:"Roboto",sans-serif;font-size:12px;font-weight:500;color:#444;text-transform:uppercase}
.main-nav span{position:absolute;white-space:nowrap}
.main-nav .active{color:var(--blue)}
.nav-divider{position:absolute;top:28px;width:1px;height:22px;background:var(--line)}
.phone{position:absolute;left:903px;top:31px;font-family:"Roboto",sans-serif;font-size:14px;color:var(--blue);white-space:nowrap}

/* hero */
.hero{position:absolute;left:0;top:81px;width:1200px;height:549px;background:linear-gradient(90deg,#f4f4f4 0%,#eceae7 40%,#d9d4cd 60%,#c8c2ba 80%,#e6e4e1 100%)}
.hero-photo{position:absolute;left:420px;top:0;width:780px;height:549px;background:radial-gradient(ellipse at 45% 40%,#c7a58c 0%,#a78b73 20%,rgba(180,170,160,.6) 45%,rgba(230,228,225,0) 75%)}
.hero-ghost{position:absolute;left:40px;top:90px;font-family:"Roboto",sans-serif;font-weight:500;color:rgba(0,0,0,.05);line-height:1}
.hero-ghost .big{font-size:230px;display:block}
.hero-ghost .small{font-size:90px;letter-spacing:60px;display:block;margin-top:-10px}
.hero-title{position:absolute;left:172px;top:240px;font-size:56px;font-weight:400;color:var(--ink)}
.hero-title em{font-style:normal;color:var(--blue)}
.hero-text{position:absolute;left:172px;top:316px;width:290px;font-size:12px;line-height:22px;color:#222}
.btn{position:absolute;display:flex;align-items:center;justify-content:center;border-radius:30px;font-family:"Roboto",sans-serif;font-size:12px;font-weight:500;color:var(--white);text-transform:uppercase}
.btn-primary{background:var(--blue)}
.btn-grey{background:var(--grey-btn)}
.slider-dots{position:absolute;left:512px;top:580px;display:flex;gap:6px}
.slider-dots i{display:block;width:40px;height:3px;background:rgba(255,255,255,.6)}
.slider-dots i.on{background:var(--white)}

/* services */
.section-title{position:absolute;left:0;width:1200px;text-align:center;font-size:32px;font-weight:400;color:var(--ink)}
.section-intro{position:absolute;left:310px;width:580px;text-align:center;font-size:12px;line-height:24px;color:#333}
.service{position:absolute;width:200px;text-align:center}
.service .icon{width:114px;height:114px;margin:0 auto;border:1.5px solid #c9c9c9;border-radius:50%;display:flex;align-items:center;justify-content:center}
.service h3{margin-top:24px;font-size:17px;font-weight:400;color:var(--ink);line-height:22px}
.service p{margin-top:8px;font-size:11.5px;line-height:20px;color:#333}

/* about band */
.about{position:absolute;left:0;top:1142px;width:1200px;height:478px;background:linear-gradient(90deg,#0f141c 0%,#243040 30%,#3a4a5c 45%,#1b2330 65%,#10151d 100%)}
.play{position:absolute;left:270px;top:325px}
.about-box{position:absolute;left:690px;top:66px;width:336px;height:361px;background:var(--blue);padding:68px 25px 0 25px;color:var(--white);overflow:hidden}
.about-box h2{font-size:30px;font-weight:400}
.about-box p{margin-top:14px;font-size:12px;line-height:23.5px}
.about-box .ghost{position:absolute;right:22px;top:250px;font-family:"Roboto",sans-serif;font-size:44px;letter-spacing:30px;color:rgba(255,255,255,.1)}
.about-box .btn{position:static;width:122px;height:36px;margin-top:24px;background:var(--white);color:var(--blue)}

/* who we are */
.card{position:absolute;width:265px}
.card .ph{width:265px;height:162px}
.card h3{margin-top:22px;font-size:16px;font-weight:400;color:var(--ink);text-transform:uppercase}
.card p{margin-top:10px;font-size:11px;line-height:21px;color:#333}
.card .btn{position:static;width:106px;height:29px;margin-top:24px;font-weight:400}

/* testimonials */
.testimonials{position:absolute;left:0;top:2140px;width:1200px;height:391px;background:var(--blue-band);overflow:hidden;color:var(--white)}
.testimonials .quote-mark{position:absolute;left:500px;top:20px;font-size:220px;line-height:1;color:rgba(0,0,0,.07);font-family:"Roboto Slab",serif}
.testimonials h2{position:absolute;left:0;top:97px;width:1200px;text-align:center;font-size:32px;font-weight:400}
.quote{position:absolute;top:176px;width:350px;text-align:center}
.quote p{font-style:italic;font-size:13px;line-height:24px}
.quote .name{margin-top:22px;font-size:16px;font-weight:700}
.quote.faded{opacity:.35}

/* footer */
.footer-col{position:absolute;top:2574px}
.footer-col h4{font-size:16px;font-weight:700;color:var(--ink)}
.footer-col ul{list-style:none;margin-top:14px}
.footer-col li{font-size:12px;line-height:21px;color:#444}
.newsletter{position:absolute;left:709px;top:2614px;width:318px;height:32px;border:1px solid #cfcfcf;border-radius:20px;overflow:hidden}
.newsletter span{position:absolute;left:14px;top:8px;font-size:11px;color:#888;font-family:"Roboto",sans-serif}
.newsletter b{position:absolute;right:0;top:0;width:84px;height:30px;background:var(--blue);color:var(--white);font-size:12px;font-weight:400;display:flex;align-items:center;justify-content:center;text-transform:uppercase;border-radius:0 20px 20px 0}
.social{position:absolute;top:2680px;width:24px;height:24px;border-radius:50%;background:#9a9a9a}
.footer-rule{position:absolute;left:172px;top:2766px;width:855px;height:1px;background:var(--line)}
.foot-brand{position:absolute;left:172px;top:2784px;color:#8f8f8f;font-weight:700;line-height:1}
.foot-brand .mark{font-size:22px;display:block}
.foot-brand .sub{font-size:8px;letter-spacing:6px;display:block;margin-top:2px}
.copyright{position:absolute;left:703px;top:2796px;font-size:11.5px;color:#333;white-space:nowrap}
</style>
</head>
<body>

<header class="site-header">
  <div class="brand"><span class="mark">Q7V</span><span class="sub">CORP</span></div>
  <nav class="main-nav">
    <span class="active" style="left:403px">Home</span>
    <span style="left:474px">Company &#9662;</span>
    <span style="left:571px">Services</span>
    <span style="left:667px">Blog</span>
    <span style="left:737px">Contact Us</span>
  </nav>
  <div class="nav-divider" style="left:836px"></div>
  <svg class="abs" style="left:854px;top:33px" width="13" height="13" viewBox="0 0 13 13"><circle cx="5.5" cy="5.5" r="4" fill="none" stroke="#333" stroke-width="1.8"/><line x1="8.5" y1="8.5" x2="12" y2="12" stroke="#333" stroke-width="1.8"/></svg>
  <div class="nav-divider" style="left:886px"></div>
  <div class="phone">&#9990; Ph: 555-014-2290</div>
</header>

<section class="hero">
  <div class="hero-photo" role="img" aria-label="Photo of a woman working on a laptop at an office desk with a plant"></div>
  <div class="hero-ghost"><span class="big">Q7V</span><span class="small">CORP</span></div>
  <h1 class="hero-title"><em>Q7V</em> Corp</h1>
  <p class="hero-text">Sed ut perspiciatis unde omnis iste natus error sit volu ptatem accusantium doloremque laudantium, totam rn aperiam, eaque ipsa quae ab illo inventore.</p>
  <div class="btn btn-primary" style="left:172px;top:316px;width:146px;height:36px;margin-top:80px">Get Started</div>
  <div class="slider-dots"><i class="on"></i><i></i><i></i></div>
</section>

<h2 class="section-title" style="top:682px">Our Services</h2>
<p class="section-intro" style="top:740px">Sed ut perspiciatis unde omnis iste natus error sit voluptatem accusantium doloremque laudantium, totam rem aperiam, eaque ipsa quae ab illo inventore veritatis et quasi architecto beatae vitae dicta sunt expli.</p>

<div class="service" style="left:165px;top:822px">
  <div class="icon"><svg width="60" height="56" viewBox="0 0 60 56" fill="none" stroke="#0d7bcb" stroke-width="2"><rect x="4" y="4" width="44" height="30" rx="2"/><line x1="26" y1="34" x2="26" y2="42"/><line x1="16" y1="42" x2="36" y2="42"/><path d="M18 14l-5 5 5 5M34 14l5 5-5 5M29 12l-6 14"/><circle cx="46" cy="44" r="7"/><circle cx="46" cy="44" r="2.5"/></svg></div>
  <h3>IT</h3>
  <p>Seciatis unde omnis iste natusit voluptatem accusantium doloremque laudantium, totam rn accusantium doloremm acc usamloreo.</p>
</div>
<div class="service" style="left:384px;top:822px">
  <div class="icon"><svg width="56" height="60" viewBox="0 0 56 60" fill="none" stroke="#0d7bcb" stroke-width="2"><rect x="8" y="4" width="40" height="12" rx="1"/><rect x="8" y="20" width="40" height="12" rx="1"/><rect x="8" y="36" width="40" height="12" rx="1"/><line x1="14" y1="10" x2="30" y2="10"/><line x1="14" y1="26" x2="30" y2="26"/><line x1="14" y1="42" x2="30" y2="42"/><line x1="28" y1="48" x2="28" y2="56"/><line x1="16" y1="56" x2="40" y2="56"/></svg></div>
  <h3>Cloud/Hosting</h3>
  <p>Seciatis unde omnis iste natusit voluptatem accusantium doloremque laudantium, totam rn accusantium doloremm acc usamloreo.</p>
</div>
<div class="service" style="left:614px;top:822px">
  <div class="icon"><svg width="62" height="56" viewBox="0 0 62 56" fill="none" stroke="#0d7bcb" stroke-width="2"><path d="M6 28L31 6l25 22"/><path d="M12 24v28h38V24"/><rect x="26" y="36" width="10" height="16"/><rect x="16" y="30" width="7" height="7"/><rect x="39" y="30" width="7" height="7"/></svg></div>
  <h3>Home/Commercial<br>Services</h3>
  <p>Seciatis unde omnis iste natusit voluptatem accusantium doloremque laudantium, totam rn accusan.</p>
</div>
<div class="service" style="left:832px;top:822px">
  <div class="icon"><svg width="60" height="60" viewBox="0 0 60 60" fill="none" stroke="#0d7bcb" stroke-width="2"><line x1="6" y1="12" x2="54" y2="12"/><line x1="24" y1="12" x2="24" y2="54"/><line x1="32" y1="12" x2="32" y2="54"/><path d="M24 20l8 8M32 28l-8 8M24 36l8 8"/><line x1="48" y1="12" x2="48" y2="26"/><rect x="42" y="26" width="12" height="8"/><line x1="16" y1="54" x2="40" y2="54"/></svg></div>
  <h3>Construction Services</h3>
  <p>Seciatis unde omnis iste natusit voluptatem accusantium doloremque laudantium, totam rn accusantium doloremm acc usamloreo.</p>
</div>

<section class="about" role="img" aria-label="Photo of a man holding a laptop in a server room">
  <svg class="play" width="110" height="110" viewBox="0 0 110 110"><circle cx="55" cy="55" r="52" fill="none" stroke="rgba(255,255,255,.35)" stroke-width="4"/><circle cx="55" cy="55" r="40" fill="#111" stroke="#fff" stroke-width="4"/><path d="M47 38l22 17-22 17z" fill="#fff"/></svg>
  <div class="about-box">
    <h2>About Q7V Corp</h2>
    <p>Lorem ipsum dolor sit amet, consectetur adipiscing dolore magna aliquat enim ad minim veniam, quid co laboris nisi ut aliuip elox ea commodo consequre din voluptateLorem ipsum dolor sit amet, consecur adipiscing elit, sed do eiumod ore et dolore.</p>
    <div class="btn">Read More</div>
    <div class="ghost">CORP</div>
  </div>
</section>

<h2 class="section-title" style="top:1682px">Who We Are</h2>
<div class="card" style="left:172px;top:1754px">
  <div class="ph" role="img" aria-label="Photo looking up at glass skyscrapers against the sun" style="background:linear-gradient(160deg,#5a6f8c 0%,#c8b8a0 45%,#a9bcd0 70%,#3e4f66 100%)"></div>
  <h3>Neque Porro Quisquam</h3>
  <p>Sed ut perspiciatis unde os istenatus error sit vol uptatem accutium doloremque laudantiuet ut per spiciatis unde os istenatus error sit vo.</p>
  <div class="btn btn-primary">Read More</div>
</div>
<div class="card" style="left:467px;top:1754px">
  <div class="ph" role="img" aria-label="Photo of a two-storey suburban house with a lawn" style="background:linear-gradient(180deg,#9cc0e0 0%,#c9d6d8 40%,#8e8a7c 65%,#4f7a3a 100%)"></div>
  <h3>Neque Porro Quisquam</h3>
  <p>Sed ut perspiciatis unde os istenatus error sit vol uptatem accutium doloremque laudantiuet ut per spiciatis unde os istenatus error sit vo.</p>
  <div class="btn btn-grey">Read More</div>
</div>
<div class="card" style="left:762px;top:1754px">
  <div class="ph" role="img" aria-label="Photo of two technicians kneeling beside server racks" style="background:linear-gradient(90deg,#1c1f24 0%,#3a3a3c 35%,#8a7560 55%,#5c6470 75%,#202328 100%)"></div>
  <h3>Neque Porro Quisquam</h3>
  <p>Sed ut perspiciatis unde os istenatus error sit vol uptatem accutium doloremque laudantiuet ut per spiciatis unde os istenatus error sit vo.</p>
  <div class="btn btn-grey">Read More</div>
</div>

<section class="testimonials">
  <div class="quote-mark">&ldquo;</div>
  <h2>Testimonials</h2>
  <div class="quote faded" style="left:30px"><p>&ldquo; Sed ut perspiciatis unde omnis iste natus error sit volu ptatem accusantium doloremque laudantium, totam rem aperiam, eaque ipsa quae ab illo inventore veritatis et qu asi architecto beatae vitae dicta sunt explica.&rdquo;</p><div class="name">Mara Quill Denton</div></div>
  <div class="quote" style="left:425px"><p>&ldquo; Sed ut perspiciatis unde omnis iste natus error sit volu ptatem accusantium doloremque laudantium, totam rem aperiam, eaque ipsa quae ab illo inventore veritatis et qu asi architecto beatae vitae dicta sunt explica.&rdquo;</p><div class="name">Mara Quill Denton</div></div>
  <div class="quote faded" style="left:820px"><p>&ldquo; Sed ut perspiciatis unde omnis iste natus error sit volu ptatem accusantium doloremque laudantium, totam rem aperiam, eaque ipsa quae ab illo inventore veritatis et qu asi architecto beatae vitae dicta sunt explica.&rdquo;</p><div class="name">Mara Quill Denton</div></div>
</section>

<footer>
  <div class="footer-col" style="left:172px"><h4>Support</h4><ul><li>Sed ut perspiciatis</li><li>Unde omnis iste</li><li>Voluptatem</li><li>Accusantium</li><li>Doloremque</li><li>Laudantium</li></ul></div>
  <div class="footer-col" style="left:352px"><h4>Company</h4><ul><li>Q7v.host</li><li>Brightwallfix</li><li>TKLS</li><li>Inc.</li><li>B&amp;J Construction</li></ul></div>
  <div class="footer-col" style="left:541px"><h4>Links</h4><ul><li>Sed ut perspiciatis</li><li>Unde omnis iste</li><li>Voluptatem</li><li>Accusantium</li><li>Doloremque</li><li>Laudantium</li></ul></div>
  <div class="footer-col" style="left:709px"><h4>Newsletter</h4></div>
  <div class="newsletter"><span>Email:</span><b>Sign Up</b></div>
  <div class="social" style="left:712px"></div>
  <div class="social" style="left:782px"></div>
  <div class="social" style="left:847px"></div>
  <div class="social" style="left:913px"></div>
  <div class="footer-rule"></div>
  <div class="foot-brand"><span class="mark">Q7V</span><span class="sub">CORP</span></div>
  <div class="copyright">&copy; 2018 All Rights Are Reserved.Terms of Use | Privacy Policy</div>
</footer>

</body>
</html>
```